New Fun, Positive, energised looking Business Card Needed for High Achiever Coach

I am looking for a two sided full colour business card. I am self employed and have recently re branded my 1-2-1 work re-vitalising high achievers. My target client base for these cards is therefore high achievers - usually aged 40 -55, they are often entrepreneurs, CEO or work in banking and finance and 2/3 are male. I work with them on 90 day or 6 month coaching programs to help them live their success in a healthier, more sustainable and fulfiiled way. They pay for this privately so though they are corporate types the cards need not look 'corporate'. I want to portray the idea of transformation, vitality and re-connecting.
You can get a feel for the look I like on my new website: morvenlisk.co.uk
I want to use this logo with strapline (Re-Vitalising High Achievers) (I purchased off Logoharbor) and font/ colours (the turquoise and green).
Details to include on the card:
www.morvenlisk.co.uk
+44 7915 302618
morven@morvenlisk.co.uk
skype: morvenlisk
I'd also like to include:
Do you struggle to switch off? Want to be healthier and feel fitter? Want closer relationships? More clarity over the direction you are headed? I can help you do these things using integrated mind-body techniques. Visit morvenlisk.co.uk TODAY to apply for a FREE Breakthrough session.
BUT if that is too much text for a card I am open to advice/ammendments.
Updates
Thanks for your design - I am considering them. PLease change the wording to :

```html
<!DOCTYPE html>
<html lang="en">
<head>
<meta charset="utf-8">
<title>Morven Lisk – Business Card</title>
<link href="https://fonts.googleapis.com/css2?family=Open+Sans:wght@400;600;700&display=swap" rel="stylesheet">
<style>
  :root {
    --turquoise: #1ba0c9;
    --green: #5cb860;
    --ink: #3f3f3f;
    --rule: #c9c9c9;
    --card: #ffffff;
    --backdrop: #ecebe7;
  }
  * { box-sizing: border-box; margin: 0; padding: 0; }
  html, body {
    width: 1200px;
    height: 720px;
    overflow: hidden;
  }
  body {
    background: var(--backdrop);
    font-family: "Open Sans", Arial, sans-serif;
    color: var(--ink);
    display: flex;
    align-items: center;
    justify-content: center;
    gap: 40px;
  }
  .card {
    width: 540px;
    height: 310px;
    background: var(--card);
    box-shadow: 0 2px 10px rgba(0,0,0,0.08);
    position: relative;
  }

  /* Front side */
  .card--front {
    display: flex;
    align-items: center;
    padding: 0 40px 0 50px;
  }
  .front-mark {
    width: 160px;
    height: 160px;
    border-radius: 50%;
    background: var(--green);
    flex: none;
  }
  .front-details {
    margin-left: 44px;
  }
  .brand-name {
    color: var(--turquoise);
    font-weight: 700;
    line-height: 1.1;
  }
  .card--front .brand-name {
    font-size: 31px;
    margin-bottom: 26px;
  }
  .contact-list {
    list-style: none;
  }
  .contact-list li {
    display: flex;
    align-items: center;
    font-size: 14.5px;
    line-height: 1;
    margin-bottom: 13px;
  }
  .contact-icon {
    width: 15px;
    height: 15px;
    margin-right: 9px;
    flex: none;
  }

  /* Back side */
  .card--back {
    display: flex;
    align-items: center;
  }
  .back-brand {
    width: 215px;
    display: flex;
    flex-direction: column;
    align-items: center;
    justify-content: center;
  }
  .back-mark {
    width: 82px;
    height: 82px;
    border-radius: 50%;
    background: var(--green);
    margin-bottom: 18px;
  }
  .card--back .brand-name {
    font-size: 24px;
  }
  .back-divider {
    width: 1px;
    align-self: stretch;
    margin: 34px 0;
    background: var(--rule);
  }
  .back-copy {
    flex: 1;
    padding: 0 24px 0 20px;
    font-size: 13px;
    line-height: 1.6;
  }
  .back-copy p + p {
    margin-top: 10px;
  }
  .back-copy strong {
    font-weight: 700;
  }
</style>
</head>
<body>

  <section class="card card--front" aria-label="Business card front">
    <div class="front-mark"></div>
    <div class="front-details">
      <div class="brand-name">Morven Lisk</div>
      <ul class="contact-list">
        <li>
          <svg class="contact-icon" viewBox="0 0 16 16" aria-hidden="true">
            <circle cx="8" cy="8" r="7.2" fill="none" stroke="var(--ink)" stroke-width="1.3"/>
            <path d="M5.4 4.3l1.3 1.6-.8 1.1c.6 1.2 1.5 2.1 2.7 2.7l1.1-.8 1.6 1.3-.7 1.3c-2.9-.3-5.5-2.9-5.8-5.8z" fill="var(--ink)"/>
          </svg>
          +44 7915 302618
        </li>
        <li>
          <svg class="contact-icon" viewBox="0 0 16 16" aria-hidden="true">
            <rect x="1.5" y="3.5" width="13" height="9" rx="1" fill="var(--ink)"/>
            <path d="M1.8 4l6.2 4.7L14.2 4" fill="none" stroke="#fff" stroke-width="1.1"/>
          </svg>
          morven@morvenlisk.co.uk
        </li>
        <li>
          <svg class="contact-icon" viewBox="0 0 16 16" aria-hidden="true">
            <circle cx="8" cy="8" r="7.2" fill="var(--ink)"/>
            <ellipse cx="8" cy="8" rx="2.8" ry="5.6" fill="none" stroke="#fff" stroke-width="0.9"/>
            <path d="M2.6 8h10.8" stroke="#fff" stroke-width="0.9"/>
          </svg>
          www.morvenlisk.co.uk
        </li>
        <li>
          <svg class="contact-icon" viewBox="0 0 16 16" aria-hidden="true">
            <rect x="1.5" y="1.5" width="13" height="13" rx="2" fill="var(--ink)"/>
          </svg>
          morvenlisk
        </li>
      </ul>
    </div>
  </section>

  <section class="card card--back" aria-label="Business card back">
    <div class="back-brand">
      <div class="back-mark"></div>
      <div class="brand-name">Morven Lisk</div>
    </div>
    <div class="back-divider"></div>
    <div class="back-copy">
      <p>Do you struggle to switch off?<br>
      Want to be healthier and feel fitter?<br>
      Want closer relationships?<br>
      More clarity over the direction you are headed?</p>
      <p>I can help you do these things using integrated mind-body techniques.</p>
      <p>Visit <strong>morvenlisk.co.uk</strong> TODAY to apply for a FREE Breakthrough session.</p>
    </div>
  </section>

</body>
</html>
```